Website for Boutique Property Consultancy in UK

We are looking to designing a website for our Property Consultancy Services that follows a minimalistic clean style that is also bold and intriguing.
The website will be based on one landing page and a link to LinkedIn Page and email link.

Dominant features will be the company logo or icon and colours.

Brand colours provided for guidance.

Looking to achieve a minimalistic clean style that is also bold and intriguing.

"Updated"
Page 1 - Landing Page with the Hyperlinks to Pick a Service, Training Portal and Quill Meadow Portal. example landing page https://brantwistle.co.uk/

Page 2 - Shows all the Services and Sectors

Target Market(s)

Occupier Clients, Tech Companies, Property Developers, Infrastructure Clients and Major Consultants

Industry/Entity Type

Construction

Coding

Coded - Design and coding required

Number of Pages Required

2 page

Font styles to use
Other font styles liked:
• Century Gothic or Futuris (Headings)

Colors
0054AA
0677BA
7BADD7
CADEEF
E8F1F8
00AB8E
00BBA5
67D7C9
C6EFE9
E9F9F6

Requirements
Must have
• Company Logo, link to enquiry and LinkedIn

```html
<!DOCTYPE html>
<html lang="en">
<head>
<meta charset="utf-8">
<title>Terra Quince — Property Consultancy</title>
<link rel="stylesheet" href="https://fonts.googleapis.com/css2?family=Didact+Gothic&display=swap">
<style>
:root{
  --green:#1ec075;
  --navy:#131338;
  --mist:#e9e9eb;
  --board:#e9e8ed;
  --white:#ffffff;
  --card:#f7f7f8;
  --rule:#c9c9cf;
  --text:#2a2a44;
}
*{box-sizing:border-box;margin:0;padding:0}
html,body{width:1200px;height:2615px;overflow:hidden;background:var(--board)}
body{font-family:"Didact Gothic","Century Gothic",sans-serif;color:var(--navy);position:relative}
.abs{position:absolute}
.accent{color:var(--green)}

/* brand board */
.board-logo{left:233px;top:136px;font-size:24px;letter-spacing:.5px}
.board-divider{width:1px;background:var(--rule);top:107px;height:94px}
.board-title{font-size:26px;top:103px}
.board-sub{font-size:16px;top:151px;color:var(--text)}
.swatch{width:42px;height:42px;border-radius:50%;top:140px}
.swatch-label{font-size:10px;top:191px;color:#555;width:60px;text-align:center}

/* site */
.site{left:222px;top:290px;width:792px;height:2225px;background:var(--white)}
.nav-logo{left:107px;top:13px;font-size:14px}
.nav-link{top:18px;font-size:8px}
.follow{left:612px;top:18px;font-size:8px}
.follow-dot{left:662px;top:11px;width:23px;height:23px;border-radius:50%;background:var(--green)}
.hero-title{left:107px;top:84px;font-size:26.5px;line-height:30px;font-weight:400}
.hero-badge{left:601px;top:88px}
.hero-photo{left:0;top:228px;width:792px;height:320px;background:linear-gradient(120deg,#c9ccd6 0%,#8a8fa2 35%,#3c4160 55%,#d9dbe3 80%,#eef0f4 100%)}
.intro{left:194px;top:604px;width:404px;text-align:center;font-size:11px;line-height:18.8px;color:var(--text)}
.intro em{font-style:italic;color:var(--navy)}

.photo{position:absolute}
.photo-contract{left:107px;top:752px;width:429px;height:401px;background:linear-gradient(135deg,#1c2344 0%,#3d4a72 45%,#c9ccd8 75%,#c7a488 100%)}
.photo-house{left:255px;top:1333px;width:429px;height:401px;background:linear-gradient(180deg,#cbbfdc 0%,#8f98b8 35%,#4d5878 65%,#7d8296 100%)}
.service-card{background:var(--card);padding:42px 0 0 35px}
.card-pre{left:434px;top:794px;width:250px;height:319px;border-right:1px solid #777}
.card-post{left:107px;top:1375px;width:252px;height:317px;border-left:1px solid #777}
.service-title{font-size:18px;line-height:19px;font-weight:400;margin-bottom:16px}
.service-list{list-style:none;font-size:8.3px;color:var(--text)}
.service-list li{height:18.3px;position:relative;padding-left:9px;white-space:nowrap}
.service-list li::before{content:"";position:absolute;left:0;top:3px;width:4px;height:4px;border-radius:50%;background:var(--green)}

.sector-title{left:143px;top:1207px;font-size:18px}
.sector-lines{left:401px;top:1246px;font-size:8px;line-height:18.3px;color:var(--text);width:284px;white-space:nowrap}

.section-rule{left:0;top:1794px;width:792px;height:1px;background:#efeff2}
.contact-title{left:0;width:792px;top:1848px;text-align:center;font-size:20px}
.field{height:11px;border-bottom:1px solid var(--green);font-size:7.5px;color:var(--text);width:197px}
.col-a{left:193px}
.col-b{left:401px}
.field-message{left:193px;top:2013px;width:405px;height:56px}
.send{left:361px;top:2092px;width:69px;height:27px;background:var(--navy);color:var(--white);font-size:7.5px;display:flex;align-items:center;justify-content:center;letter-spacing:.2px}
.copyright{left:0;width:792px;top:2158px;text-align:center;font-size:6.5px;color:#888}
</style>
</head>
<body>

<!-- brand board -->
<div class="abs board-logo">terra quince</div>
<div class="abs board-divider" style="left:485px"></div>
<div class="abs board-title" style="left:582px">Fonts</div>
<div class="abs board-sub" style="left:582px">Century Gothic</div>
<div class="abs board-divider" style="left:788px"></div>
<div class="abs board-title" style="left:884px">Colors:</div>
<div class="abs swatch" style="left:885px;background:var(--green)"></div>
<div class="abs swatch" style="left:938px;background:var(--navy)"></div>
<div class="abs swatch" style="left:993px;background:var(--mist);border:1px solid #f4f4f6"></div>
<div class="abs swatch-label" style="left:876px">#1ec075</div>
<div class="abs swatch-label" style="left:929px">#131338</div>
<div class="abs swatch-label" style="left:984px">#e9e9eb</div>

<!-- landing page -->
<main class="abs site">
  <header>
    <div class="abs nav-logo">terra quince</div>
    <nav>
      <span class="abs nav-link" style="left:346px">Home</span>
      <span class="abs nav-link" style="left:387px">Services</span>
      <span class="abs nav-link" style="left:433px">Contact</span>
    </nav>
    <span class="abs follow">Follow Us:</span>
    <span class="abs follow-dot" aria-label="Professional network profile"></span>
  </header>

  <h1 class="abs hero-title">Property <span class="accent">Consultancy</span><br>Services for Your<br>Real Estate Needs</h1>
  <svg class="abs hero-badge" width="86" height="86" viewBox="0 0 86 86" aria-hidden="true">
    <circle cx="43" cy="43" r="41.5" fill="none" stroke="#555" stroke-width="1"/>
    <path d="M37 41 L40 49 L49 37" fill="none" stroke="var(--green)" stroke-width="1.6"/>
  </svg>

  <div class="abs hero-photo" role="img" aria-label="Photo of two consultants reviewing plans in a bright empty office"></div>

  <p class="abs intro">At our boutique property consultancy company, we pride ourselves on delivering bespoke solutions that are tailored to meet the <em>unique needs of our clients.</em> With a deep understanding of the local property market, we provide expert advice on a wide range of property-related matters, including sales, leasing, property management, and development</p>

  <div class="photo photo-contract" role="img" aria-label="Photo of a hand signing a contract with a pen"></div>
  <section class="abs service-card card-pre">
    <h2 class="service-title">01. Pre-<span class="accent">Contract</span><br>Services</h2>
    <ul class="service-list">
      <li>Specialised MEP Cost Management</li>
      <li>Programme Cost Assurance</li>
      <li>Strategic PMO Cost Advisory</li>
      <li>Benchmarking and Market Insight</li>
      <li>Development Appraisals &amp; Cost Modelling</li>
      <li>Feasibility Studies and Cost Planning</li>
      <li>Procurement and Tendering</li>
      <li>Contractual Advice (BCF, ICSA, PCF3, PCF4)</li>
      <li>Value Engineering and Lifecycle costing</li>
    </ul>
  </section>

  <h2 class="abs sector-title" style="font-weight:400">Sector <span class="accent">Experience</span></h2>
  <div class="abs sector-lines">
    - Commercial Offices; Retail; Residential; Hotels; Mixed Use; Industrial Parks<br>
    - Infrastructure; Eastline; Trackway Group; NR5 and CTB
  </div>

  <div class="photo photo-house" role="img" aria-label="Photo of a detached house with a double garage at dusk"></div>
  <section class="abs service-card card-post">
    <h2 class="service-title">02. Post <span class="accent">Contract</span><br>Services</h2>
    <ul class="service-list">
      <li>Commercial Management</li>
      <li>Cost Governance/Assurance/Auditing</li>
      <li>Contract Administration</li>
      <li>Change Management</li>
      <li>Fund Monitoring</li>
      <li>Final Account Closeout</li>
      <li>Claims and Dispute Resolution</li>
    </ul>
  </section>

  <div class="abs section-rule"></div>

  <section class="contact">
    <h2 class="abs contact-title" style="font-weight:400">Drop Us a Line</h2>
    <div class="abs field col-a" style="top:1898px">First Name*</div>
    <div class="abs field col-b" style="top:1898px">Last Name*</div>
    <div class="abs field col-a" style="top:1937px">Email Address*</div>
    <div class="abs field col-b" style="top:1937px">Phone Number*</div>
    <div class="abs field col-a" style="top:1975px">Subject</div>
    <div class="abs field col-b" style="top:1975px">Type of Service*</div>
    <div class="abs field field-message">Message</div>
    <div class="abs send">SEND FORM</div>
  </section>

  <footer class="abs copyright">© 2023 - TerraQuince</footer>
</main>

</body>
</html>
```